Weightloss company needs Business Card

We want a business card that is clean and professional, yet portrays that we are a friendly, innovative, and versatile program designed to fit the needs of our clients.
I would like there to be 2 sides, one side having an appointment card, and the other side containing the logo and business information. There can be decorations on both sides. The logo is attached.

Target Market(s)

Men and women 40-60

Industry/Entity Type

Business

Contact Information for Business Card

Font styles to use
Sans Serif

Requirements
Must have
• The logo, space for business information
Nice to have
• The colors in the logo
Should not have
• No pictures of people or food

```html
<!DOCTYPE html>
<html lang="en">
<head>
<meta charset="utf-8">
<title>Northfield Health Co. – Business Card</title>
<link rel="stylesheet" href="https://fonts.googleapis.com/css2?family=Open+Sans:wght@400;600;700&display=swap">
<style>
  :root {
    --page-bg: #e9e7e4;
    --card-white: #ffffff;
    --card-dark: #2f2f31;
    --brand-red: #e3163c;
    --ink: #222222;
    --dots: #555555;
  }
  * { box-sizing: border-box; margin: 0; padding: 0; }
  html, body {
    width: 1200px; height: 844px; overflow: hidden;
    background: var(--page-bg);
    font-family: "Open Sans", sans-serif;
  }
  .card-set {
    position: absolute; top: 0; left: 0; width: 1200px; height: 844px;
    display: flex; align-items: center; justify-content: center; gap: 44px;
  }
  .card {
    position: relative; width: 520px; height: 298px;
    box-shadow: 0 4px 14px rgba(0,0,0,.18);
    overflow: hidden;
  }

  /* Front: brand and contact */
  .card-front { background: var(--card-white); color: var(--ink); }
  .brand {
    position: absolute; top: 44px; right: 34px;
    display: flex; align-items: center; gap: 10px;
  }
  .brand-mark { width: 14px; height: 14px; border-radius: 50%; background: var(--brand-red); }
  .brand-name {
    font-weight: 700; font-size: 24px; color: var(--brand-red); letter-spacing: -.2px;
    white-space: nowrap;
  }
  .contact { position: absolute; left: 34px; bottom: 30px; font-size: 14px; line-height: 1.45; }
  .contact-name { color: var(--brand-red); font-weight: 600; font-size: 17px; }
  .contact-role { margin-bottom: 16px; }
  .contact-address { margin-bottom: 14px; }
  .label { color: var(--brand-red); }
  .web { color: var(--brand-red); }

  /* Back: appointment */
  .card-back { background: var(--card-dark); color: #fff; }
  .appt-heading {
    position: absolute; top: 0; left: 0; right: 0; height: 50px;
    display: flex; align-items: flex-end; justify-content: center; padding-bottom: 8px;
    font-weight: 600; font-size: 14px; letter-spacing: .5px; text-transform: uppercase;
  }
  .appt-band {
    position: absolute; top: 58px; left: 0; right: 0; height: 150px;
    background: var(--card-white);
    padding: 26px 40px 0 48px;
    display: flex; flex-direction: column; gap: 18px;
  }
  .field { display: flex; align-items: baseline; font-size: 13px; color: var(--ink); }
  .field-label { color: var(--brand-red); font-weight: 600; margin-right: 6px; }
  .field-line { flex: 1; border-bottom: 2px dotted var(--dots); height: 12px; }
  .field-unit { font-weight: 600; font-size: 12px; margin: 0 4px; }
  .appt-note {
    position: absolute; left: 0; right: 0; bottom: 38px;
    text-align: center; font-weight: 600; font-size: 13px; line-height: 1.5;
    letter-spacing: .3px; text-transform: uppercase;
  }
</style>
</head>
<body>
  <main class="card-set">
    <section class="card card-front" aria-label="Business card front">
      <div class="brand">
        <span class="brand-mark" aria-hidden="true"></span>
        <span class="brand-name">Northfield Health Co.</span>
      </div>
      <div class="contact">
        <p class="contact-name">John Smith</p>
        <p class="contact-role">Managing Director</p>
        <p class="contact-address">1234, Address GoesHere, Country, 12345</p>
        <p><span class="label">T:</span>(044) 123 456 789 &nbsp;<span class="label">F:</span>(044) 123456789 &nbsp;<span class="label">M:</span>(044)123456789</p>
        <p><span class="label">E:</span>info@youremail.com &nbsp; <span class="web">www.yourweb.com</span></p>
      </div>
    </section>

    <section class="card card-back" aria-label="Appointment card">
      <h2 class="appt-heading">Your next appointment is</h2>
      <div class="appt-band">
        <div class="field"><span class="field-label">Name:</span><span class="field-line"></span></div>
        <div class="field"><span class="field-label">Date:</span><span class="field-line"></span></div>
        <div class="field"><span class="field-label">Time:</span><span class="field-line"></span><span class="field-unit">AM</span><span class="field-line"></span><span class="field-unit">PM</span></div>
      </div>
      <p class="appt-note">If unable to keep appointment,<br>kindly give 24hrs notice.</p>
    </section>
  </main>
</body>
</html>
```